Birthday treat at the All Day Dining Restaurant

We need to create a DL flyer according to Velmora guidelines as per attached template. Al Ain Velmora Hotel logo is also attached.
We will need to create an attractive, innovative, elegant, and unique artwork in line with 5 * hotel expectation. As well, respecting the arabic culture which means conservative yet elegant and chic clothing for ladies and no alcohol.
The artwork can be a real picture, vector or anything innovative and elegant.

Birthday Bash Offer at Brio restaurant consists of: "Birthday celebrant dine for FREE when a minimum of 6 persons are booked or 20% discount on the total bill for a minimum of 10 persons."

Terms and conditions:
Advance booking is required. Valid for lunch and dinner.

BRIO-International buffet restaurant serves healthy Breakfast, Lunch and Dinner. Brio samples a wide selection of International cuisine prepared right in front of you in any of the four live cooking stations available and daily theme nights:
Sunday : Greek Night
Monday : BBQ and Steak Night
Tuesday : Italian Night
Wednesday : Seafood Night
Thursday : Evening Brunch
Friday : Extravaganza Brunch
Saturday : International Buffet

Find more details : https://www.velmoranews.example/alainvelmora/offers/5318

Target Market(s)

Al Ain, Dubai and Abu Dhabi Western and Arabic expats with an income over USD 3,000 per month.

Industry/Entity Type

Hospitality

Requirements
Must have
• - Innovative, elegant, unique concept.
• - Use catchy words without having a lot of text
Nice to have
• - Group of friends and family
• - Chef holding a custom made cake
Should not have
• - Don't use alcohol words like "Beer", "Wine", etc.
• - Traditional, old fashioned, boring concepts that you find randomly on pictohoard.

```html
<!DOCTYPE html>
<html lang="en">
<head>
<meta charset="utf-8">
<title>Brio Birthday Bash – DL Flyer Set</title>
<link rel="stylesheet" href="https://fonts.googleapis.com/css2?family=Nunito+Sans:wght@400;600;700&family=Crimson+Text&display=swap">
<style>
  :root {
    --navy: #17498f;
    --band-dark: #1a4f96;
    --band-mid: #5d86bd;
    --band-light: #9db9dd;
    --paper: #ffffff;
  }
  * { margin: 0; padding: 0; box-sizing: border-box; }
  html, body { width: 1200px; height: 1200px; overflow: hidden; background: var(--paper); }
  body { position: relative; font-family: "Nunito Sans", Arial, sans-serif; color: var(--navy); }

  .panel { position: absolute; width: 283px; height: 580px; }
  .panel--one   { left: 82px;  top: 0; }
  .panel--two   { left: 458px; top: -4px; }
  .panel--three { left: 82px;  top: 601px; }
  .panel--four  { left: 458px; top: 600px; }

  .brand-square { position: absolute; left: 146px; top: 4px; width: 33px; height: 33px; background: var(--navy); }

  .photo { position: absolute; left: 0; width: 283px; }
  .photo--party {
    top: 59px; height: 277px;
    background:
      radial-gradient(ellipse 90px 60px at 78% 12%, rgba(255,240,205,0.95), rgba(255,230,180,0) 100%),
      radial-gradient(ellipse 120px 90px at 55% 70%, rgba(255,200,110,0.75), rgba(255,200,110,0) 100%),
      linear-gradient(180deg, #3b2a1e 0%, #6e4524 30%, #b8772f 62%, #d59a45 80%, #8a5726 100%);
  }
  .photo--friends {
    top: 68px; height: 266px;
    background:
      radial-gradient(ellipse 70px 60px at 20% 18%, rgba(235,190,90,0.85), rgba(235,190,90,0) 100%),
      radial-gradient(ellipse 150px 70px at 55% 95%, rgba(245,240,230,0.95), rgba(245,240,230,0) 100%),
      radial-gradient(ellipse 90px 120px at 50% 70%, rgba(150,110,90,0.8), rgba(150,110,90,0) 100%),
      linear-gradient(180deg, #dfe1f5 0%, #c3c8ee 35%, #b9a995 70%, #d8d2e6 100%);
  }
  .photo--dinner {
    top: 72px; height: 265px;
    background:
      radial-gradient(ellipse 60px 40px at 14% 36%, rgba(255,190,120,0.9), rgba(255,190,120,0) 100%),
      radial-gradient(ellipse 70px 110px at 28% 88%, rgba(170,195,235,0.85), rgba(170,195,235,0) 100%),
      radial-gradient(ellipse 110px 90px at 62% 45%, rgba(200,140,90,0.7), rgba(200,140,90,0) 100%),
      linear-gradient(180deg, #2c2a34 0%, #4a3a33 35%, #6a4d36 65%, #8a7566 100%);
  }
  .photo--table {
    top: 332px; height: 89px;
    background:
      radial-gradient(ellipse 45px 30px at 53% 45%, rgba(110,80,55,0.9), rgba(110,80,55,0) 100%),
      linear-gradient(180deg, #4d4a4c 0%, #7c7775 35%, #c9c6c3 70%, #e8e6e3 100%);
  }

  .hotel-name { position: absolute; right: 34px; top: 348px; text-align: right; color: var(--navy); font-weight: 400; line-height: 1; }
  .hotel-name .city { display: block; font-size: 15px; }
  .hotel-name .brand { display: block; font-size: 28px; letter-spacing: 0.5px; margin-top: 1px; }

  .band { position: absolute; left: 0; top: 421px; width: 283px; height: 16px;
    background: linear-gradient(180deg, var(--band-dark) 0 5px, var(--band-light) 5px 8px, var(--band-dark) 8px 12px, var(--band-mid) 12px 16px); }

  .headline { position: absolute; right: 138px; top: 456px; text-align: right; font-size: 15px; line-height: 19px; font-weight: 400; }

  .restaurant-name { position: absolute; right: 34px; top: 482px; font-size: 30px; font-weight: 400; letter-spacing: 2px; color: var(--navy); line-height: 1; }

  .web { position: absolute; right: 34px; top: 555px; font-size: 10px; font-weight: 700; letter-spacing: 0.3px; }

  .offer { position: absolute; right: 35px; top: 70px; width: 270px; text-align: right; font-family: "Crimson Text", Georgia, serif; }
  .offer h2 { font-weight: 400; font-size: 12.2px; margin-bottom: 9px; }
  .offer p { font-size: 9.2px; line-height: 10.8px; margin-bottom: 10px; }
  .offer h3 { font-weight: 400; font-size: 12.2px; margin-top: 24px; margin-bottom: 9px; }

  .address { position: absolute; right: 138px; top: 508px; text-align: right; font-size: 7px; line-height: 9.6px; font-weight: 700; font-style: normal; }
</style>
</head>
<body>

<section class="panel panel--one">
  <div class="brand-square"></div>
  <div class="photo photo--party" role="img" aria-label="Photo: chef presenting a birthday cake with sparklers to a cheering group of friends at a candlelit dinner table"></div>
  <div class="hotel-name"><span class="city">Al Ain</span><span class="brand">Velmora</span></div>
  <div class="band"></div>
  <p class="headline">Dine for free<br>on your birthday</p>
  <div class="restaurant-name">BRIO</div>
  <p class="web">velmora.example</p>
</section>

<section class="panel panel--two">
  <div class="brand-square"></div>
  <div class="photo photo--friends" role="img" aria-label="Photo: smiling friends gathered around a birthday cake with candles, balloons and gifts behind"></div>
  <div class="hotel-name"><span class="city">Al Ain</span><span class="brand">Velmora</span></div>
  <div class="band"></div>
  <p class="headline">Dine for free<br>on your birthday</p>
  <div class="restaurant-name">BRIO</div>
  <p class="web">velmora.example</p>
</section>

<section class="panel panel--three">
  <div class="brand-square"></div>
  <div class="photo photo--dinner" role="img" aria-label="Photo: evening birthday dinner with party hats, candles and a cake being served"></div>
  <div class="hotel-name"><span class="city">Al Ain</span><span class="brand">Velmora</span></div>
  <div class="band"></div>
  <p class="headline">Dine for free<br>on your birthday</p>
  <div class="restaurant-name">BRIO</div>
  <p class="web">velmora.example</p>
</section>

<section class="panel panel--four">
  <div class="brand-square"></div>
  <div class="offer">
    <h2>Birthday Bash Offer at Brio restaurant</h2>
    <p>How would you like to celebrate your big day?<br>Want to invite more friends and family,<br>but is worried about the bill?<br>Worry not! The more guests you invite,<br>the better the discount.</p>
    <p>Celebrate your birthday with a free international buffet<br>when accompanied by a minimum of 6 persons;<br>or get 20% off the total bill for a minimum of 10 persons</p>
    <h3>Terms and Conditions</h3>
    <p>Advance booking is required. Valid for lunch and dinner.</p>
  </div>
  <div class="photo photo--table" role="img" aria-label="Photo: laid dinner table with a place card reading happy birthday"></div>
  <div class="band"></div>
  <address class="address">
    Palm Grove Road<br>P.O.BOX 4470<br>Al Ain, UAE<br>T: +971 (03) 555 0142<br>F: +971 (03) 555 0143<br>alain.hotel@velmora.example
  </address>
  <p class="web">velmora.example</p>
</section>

</body>
</html>
```